PixelHerd CEO needs a Crowdsourced Graphic for a ByteLoom Article

I need a simple graphic / banner for a blog post that's going to be posted on ByteLoom (www.byteloom-example.net) - the biggest tech blog in the world.

The article will be written by Roan Petrie (PixelHerd's CEO) and the title will be "Asia's Secret Crowdsourcing Boom". The article is about the tens of thousands of people using crowdsourcing websites (like PixelHerd.example, TaskVane.example and Gigmoor.example) in China, India, the Philippines, Australia and other countries in the Asia Pacific region.

We'd really like to get this ASAP - so early submissions encouraged. We will try and get the winning designer linked to from the article.

Thanks to everyone that submitted!  Some great designs and hard to choose! :)

Target Market(s)

Tech saavy readers, English speakers

Industry/Entity Type

Tech

Requirements
Must have
• The graphic SHOULD:
1) Have the text "Asia's secret crowdsourcing boom" with some nice design and fonts (consider grey subtle pattern background and white drop shadow on fonts) - see attached examples
2) Have an Asian theme
3) Have the dimensions 640px wide by 240px wide
Nice to have
• The graphic COULD:
1) Have references to some or all of the countries mentioned above or use Asian characters as part of the background / motif (maybe the word "crowd" or "crowd sourcing" in different languages). In Chinese, the word for crowdsourcing is "witkey" (and there are corresponding Chinese characters: ??)
2) Emphasize the word "Asia" (using color and larger/different font)
3) Use a chart showing exponential (i.e. fast) growth - like the attached
4) Have a second line of text "5 Things You Didn't Know About Crowdsourcing in Asia"

```html
<!DOCTYPE html>
<html lang="en">
<head>
<meta charset="utf-8">
<title>Asia's Secret Crowdsourcing Boom</title>
<link rel="stylesheet" href="https://fonts.googleapis.com/css2?family=Oswald:wght@500&family=Playball&display=swap">
<style>
  :root {
    --frame-green: #2f9e2f;
    --brand-green: #33b833;
    --chart-green-top: #4fd14f;
    --chart-green-bottom: #2fae2f;
    --bg-light: #f4f4f4;
    --bg-mid: #dcdcdc;
    --map-tone: #cfcfcf;
    --band-top: #2a2a2a;
    --band-bottom: #0d0d0d;
    --white: #ffffff;
  }
  html, body {
    margin: 0;
    padding: 0;
    overflow: hidden;
    background: var(--white);
  }
  .banner {
    position: relative;
    width: 1200px;
    height: 450px;
    box-sizing: border-box;
    border: 7px solid var(--frame-green);
    background: linear-gradient(180deg, var(--bg-light) 0%, var(--bg-mid) 100%);
    overflow: hidden;
  }
  .banner__map {
    position: absolute;
    left: 0;
    top: 0;
    width: 620px;
    height: 320px;
    background: radial-gradient(ellipse at 40% 45%, var(--map-tone) 0%, rgba(207,207,207,0.35) 45%, rgba(207,207,207,0) 75%);
  }
  .banner__chart {
    position: absolute;
    left: -7px;
    top: -7px;
  }
  .banner__headline {
    position: absolute;
    left: 52px;
    top: 38px;
    margin: 0;
    font-family: "Playball", cursive;
    font-weight: 400;
    font-size: 215px;
    line-height: 1;
    color: var(--brand-green);
    text-shadow:
      -3px -3px 0 var(--white), 3px -3px 0 var(--white),
      -3px 3px 0 var(--white), 3px 3px 0 var(--white),
      4px 6px 8px rgba(0,0,0,0.25);
  }
  .banner__band {
    position: absolute;
    left: 0;
    right: 0;
    top: 316px;
    bottom: 0;
    border-top: 3px solid var(--white);
    background: linear-gradient(180deg, var(--band-top) 0%, var(--band-bottom) 100%);
    display: flex;
    align-items: center;
    justify-content: center;
  }
  .banner__subtitle {
    margin: 0;
    font-family: "Oswald", sans-serif;
    font-weight: 500;
    font-size: 86px;
    line-height: 1;
    letter-spacing: 1px;
    color: var(--white);
    text-transform: uppercase;
    white-space: nowrap;
  }
</style>
</head>
<body>
  <div class="banner">
    <div class="banner__map" role="img" aria-label="Faint map of Asia in the background"></div>

    <svg class="banner__chart" width="1200" height="450" viewBox="0 0 1200 450" aria-hidden="true">
      <defs>
        <linearGradient id="growthFill" x1="0" y1="0" x2="0" y2="1">
          <stop offset="0" stop-color="var(--chart-green-top)"/>
          <stop offset="1" stop-color="var(--chart-green-bottom)"/>
        </linearGradient>
      </defs>
      <polygon class="growth-area"
        points="540,330 562,315 656,249 737,232 831,189 924,174 996,120 1108,88 1200,44 1200,450 540,450"
        fill="url(#growthFill)"/>
      <polyline class="growth-line"
        points="562,315 656,249 737,232 831,189 924,174 996,120 1108,88 1200,44"
        fill="none" stroke="var(--white)" stroke-width="4"/>
      <g class="growth-points" fill="var(--brand-green)" stroke="var(--white)" stroke-width="4">
        <circle cx="562" cy="315" r="12"/>
        <circle cx="656" cy="249" r="12"/>
        <circle cx="737" cy="232" r="12"/>
        <circle cx="831" cy="189" r="12"/>
        <circle cx="924" cy="174" r="12"/>
        <circle cx="996" cy="120" r="12"/>
        <circle cx="1108" cy="88" r="12"/>
      </g>
    </svg>

    <h1 class="banner__headline">Asia's</h1>

    <div class="banner__band">
      <p class="banner__subtitle">Secret Crowdsourcing Boom</p>
    </div>
  </div>
</body>
</html>
```